Thornvale Group needs a business card design

We need a new business card design using the logo recently selected in a logo competition on Pixel Bazaar. Our business is a consultancy specializing in aviation and energy and the winning business card design will promote an image of precision and professionalism with creativity.

Please use the logo with the name on the front of the card and use a complementary font. Make the back white with either the light grey or dark grey logo.

Target Market(s)

Senior finance and legal leaders at aviation and energy companies

Industry/Entity Type

Management Consulting

Contact Information for Business Card

Peter Castrell
President
Thornvale Group

www.thornvalegroup.example

(555) 204-6391
pc@thornvalegroup.example

Requirements
Must have
• Professional font that goes well with the logo font

```html
<!DOCTYPE html>
<html lang="en">
<head>
<meta charset="utf-8">
<title>Thornvale Group – Business Card</title>
<link rel="stylesheet" href="https://fonts.googleapis.com/css2?family=Jost:wght@400&family=PT+Sans:wght@400&display=swap">
<style>
  :root {
    --backdrop: #ff7a3a;
    --brand-blue: #052e94;
    --card-white: #ffffff;
    --back-white: #fbfbfb;
    --mark-grey: #52626a;
    --text-light: #ffffff;
  }
  * { margin: 0; padding: 0; box-sizing: border-box; }
  html, body {
    width: 1056px; height: 1200px; overflow: hidden;
    background: var(--backdrop);
  }
  .canvas { position: relative; width: 1056px; height: 1200px; }
  .card {
    position: absolute; left: 36px; width: 978px; height: 558px; overflow: hidden;
  }
  .card--front { top: 23px; background: var(--card-white); }
  .card--back { top: 613px; background: var(--back-white); }

  .wave { position: absolute; inset: 0; width: 978px; height: 558px; }

  .brand {
    position: absolute; right: 61px; top: 140px;
    font-family: "Jost", sans-serif; font-weight: 400;
    color: var(--brand-blue); text-align: center; line-height: 1;
  }
  .brand__name { display: block; font-size: 30px; letter-spacing: 1px; }
  .brand__sub { display: block; font-size: 15px; letter-spacing: 17px; margin-top: 14px; padding-left: 17px; }

  .contacts {
    position: absolute; left: 49px; top: 420px; list-style: none;
    font-family: "PT Sans", sans-serif; font-size: 21px; color: var(--text-light);
  }
  .contacts__item { display: flex; align-items: center; height: 35px; }
  .contacts__icon { width: 24px; height: 24px; margin-right: 17px; flex: none; }

  .person {
    position: absolute; right: 61px; top: 412px; text-align: right;
    color: var(--text-light);
  }
  .person__name {
    font-family: "Jost", sans-serif; font-weight: 400;
    font-size: 38px; font-variant: small-caps; letter-spacing: 2px; line-height: 1;
    padding-bottom: 3px; border-bottom: 1px solid var(--text-light);
  }
  .person__role, .person__company {
    font-family: "PT Sans", sans-serif; font-size: 26px; line-height: 28px; letter-spacing: 0.5px;
  }
  .person__role { margin-top: 4px; }
  .person__company { letter-spacing: 1.5px; }

  .back-name {
    position: absolute; left: 0; right: 0; top: 0; bottom: 0;
    display: flex; align-items: center; justify-content: center;
    font-family: "Jost", sans-serif; font-weight: 400;
    font-size: 84px; letter-spacing: 3px; color: var(--mark-grey);
  }
</style>
</head>
<body>
<main class="canvas">
  <section class="card card--front">
    <svg class="wave" viewBox="0 0 978 558" aria-hidden="true">
      <path d="M0 64 C 160 25, 380 40, 600 160 S 880 280, 978 307 L978 558 L0 558 Z" fill="var(--brand-blue)"/>
    </svg>

    <div class="brand">
      <span class="brand__name">THORNVALE</span>
      <span class="brand__sub">GROUP</span>
    </div>

    <ul class="contacts">
      <li class="contacts__item">
        <svg class="contacts__icon" viewBox="0 0 24 24" fill="none" stroke="#fff" stroke-width="1.8" aria-hidden="true">
          <rect x="6" y="2" width="12" height="20" rx="2"/><line x1="10" y1="18.5" x2="14" y2="18.5"/>
        </svg>
        (555) 204-6391
      </li>
      <li class="contacts__item">
        <svg class="contacts__icon" viewBox="0 0 24 24" fill="none" stroke="#fff" stroke-width="1.8" aria-hidden="true">
          <rect x="2" y="5" width="20" height="14"/><polyline points="2,5 12,13 22,5"/>
        </svg>
        pc@thornvalegroup.example
      </li>
      <li class="contacts__item">
        <svg class="contacts__icon" viewBox="0 0 24 24" fill="none" stroke="#fff" stroke-width="1.8" aria-hidden="true">
          <rect x="2" y="4" width="20" height="16" rx="1"/><line x1="2" y1="8" x2="22" y2="8"/><line x1="6" y1="14" x2="18" y2="14"/>
        </svg>
        www.thornvalegroup.example
      </li>
    </ul>

    <div class="person">
      <p class="person__name">Peter Castrell</p>
      <p class="person__role">President</p>
      <p class="person__company">Thornvale Group</p>
    </div>
  </section>

  <section class="card card--back">
    <p class="back-name">Thornvale Group</p>
  </section>
</main>
</body>
</html>
```